Business Card Design

I already have a company logo for my company. I have a logo for the manufacturer we represent. I want a professional business card design.

```html
<!DOCTYPE html>
<html lang="en">
<head>
<meta charset="utf-8">
<title>Beacon Alert Co — Business Card</title>
<link rel="stylesheet" href="https://fonts.googleapis.com/css2?family=Open+Sans:wght@400;600;700;800&display=swap">
<style>
  :root {
    --backdrop: #222222;
    --card-dark: #1d1d22;
    --gold: #b98c2f;
    --red: #e3232b;
    --white: #ffffff;
    --silver: #c9c9cc;
    --shadow: rgba(0, 0, 0, 0.55);
  }
  * { margin: 0; padding: 0; box-sizing: border-box; }
  html, body {
    width: 1200px; height: 780px; overflow: hidden;
    background: var(--backdrop);
    font-family: "Open Sans", Arial, sans-serif;
  }
  .canvas {
    position: relative; width: 1200px; height: 780px;
    display: flex; align-items: center; justify-content: center; gap: 60px;
  }
  .card {
    position: relative; width: 520px; height: 300px;
    border-radius: 22px; overflow: hidden;
    background: var(--card-dark);
    box-shadow: 0 18px 40px var(--shadow);
  }
  .card-front .wave { position: absolute; inset: 0; width: 100%; height: 100%; }

  .contact-block {
    position: absolute; left: 30px; top: 34px; color: var(--white);
  }
  .person-name { font-size: 24px; font-weight: 800; letter-spacing: 0.2px; line-height: 1.1; }
  .person-name .first { color: var(--red); }
  .person-role { font-size: 13px; font-weight: 600; margin-top: 4px; }
  .address { font-size: 12px; line-height: 1.45; margin-top: 14px; }
  .contact-list { list-style: none; margin-top: 12px; font-size: 12px; line-height: 1.75; }
  .contact-list li { display: flex; align-items: center; gap: 8px; }
  .contact-list svg { width: 12px; height: 12px; flex: none; }

  .brand {
    position: absolute; display: flex; align-items: center; gap: 12px;
    font-weight: 800; text-transform: uppercase; letter-spacing: 1.5px;
  }
  .card-front .brand { right: 34px; top: 122px; color: var(--white); font-size: 22px; }
  .brand-dot { width: 16px; height: 16px; border-radius: 50%; background: var(--red); flex: none; }

  .card-back .brand {
    left: 50%; top: 50%; transform: translate(-50%, -50%);
    color: var(--silver); font-size: 30px; white-space: nowrap;
  }
  .card-back .brand-dot { width: 22px; height: 22px; background: var(--silver); }
</style>
</head>
<body>
<main class="canvas">

  <section class="card card-front" aria-label="Card front">
    <svg class="wave" viewBox="0 0 520 300" preserveAspectRatio="none" aria-hidden="true">
      <path d="M0 0 H212 C282 0 268 140 318 224 C346 272 382 300 400 300 H0 Z" fill="var(--red)"/>
      <path d="M0 0 H200 C268 0 254 142 302 226 C330 274 362 300 378 300 H0 Z" fill="var(--card-dark)"/>
      <path d="M0 0 H188 C254 0 244 146 290 228 C316 274 344 300 358 300 H0 Z" fill="var(--gold)"/>
      <path d="M232 40 C262 110 268 190 330 268" fill="none" stroke="var(--card-dark)" stroke-width="2"/>
    </svg>

    <div class="contact-block">
      <h1 class="person-name"><span class="first">Marta</span> Velinska</h1>
      <p class="person-role">Managing Director</p>
      <p class="address">418 Harlow Ave. Suite 120<br>Denton, TX 76201</p>
      <ul class="contact-list">
        <li>
          <svg viewBox="0 0 24 24"><path fill="var(--red)" d="M6.6 10.8a15.1 15.1 0 0 0 6.6 6.6l2.2-2.2a1 1 0 0 1 1-.25 11.4 11.4 0 0 0 3.6.57 1 1 0 0 1 1 1V20a1 1 0 0 1-1 1A17 17 0 0 1 3 4a1 1 0 0 1 1-1h3.5a1 1 0 0 1 1 1c0 1.25.2 2.45.57 3.57a1 1 0 0 1-.25 1z"/></svg>
          (940) 555-0147
        </li>
        <li>
          <svg viewBox="0 0 24 24"><rect x="2" y="5" width="20" height="14" rx="2" fill="var(--red)"/><path d="M3 6l9 7 9-7" fill="none" stroke="var(--gold)" stroke-width="2"/></svg>
          hello@beaconalert.com
        </li>
        <li>
          <svg viewBox="0 0 24 24"><circle cx="12" cy="12" r="10" fill="var(--red)"/><path d="M2 12h20M12 2c3 3 3 17 0 20M12 2c-3 3-3 17 0 20" fill="none" stroke="var(--gold)" stroke-width="1.5"/></svg>
          www.beaconalert.com
        </li>
      </ul>
    </div>

    <div class="brand"><span class="brand-dot"></span>Beacon Alert Co</div>
  </section>

  <section class="card card-back" aria-label="Card back">
    <div class="brand"><span class="brand-dot"></span>Beacon Alert Co</div>
  </section>

</main>
</body>
</html>
```